A specialised Sport management needs a corporate brochure design

We are a specialized company in the management and consultancy of sports events. and need to have a company brochure
We provide the following services;
Event management
Venues management
Production
Ticketing
Consulting
Hospitality
Activity management
Event timing
Branding of event
Event supplies
We need a corporate profile design for our company to showcase the major events that we have covered , with images, information, statistics, surveys, products and services used. We want to highlight our professionalism and execution of the events, experience of the participants, spectators . How we have grown in the past few years and reached the international standards.
Objectives of the work:
To get sponsors and partners for future business and to present Tri-Crest
as not just a sports management company but also a professional sports
events management company.
You can check our website
www.tri-crest.example
Target Market(s)
Sponsors and corporate partners
Industry/Entity Type
Events
Requirements
Must have
- Must Have:
- - Very professional look
- -Some event images,Event information, statistics, surveys, products and services used. We want to highlight our professionalism and execution of the events (Attached)
Nice to have
- Similar momentom of the below design
- http://www.lumavent.example/wp-content/themes/lumavent/pdf/CP-2014-15-V10-Web.pdf

```html
<!DOCTYPE html>
<html lang="en">
<head>
<meta charset="utf-8">
<title>Tri-Crest — Target Segment &amp; Growth</title>
<link rel="stylesheet" href="https://fonts.googleapis.com/css2?family=Oswald:wght@500;700&family=Roboto:wght@400;700&display=swap">
<style>
  :root{
    --stage:#000000;
    --orange:#f05a28;
    --orange-deep:#e2461b;
    --green:#1f7a3d;
    --green-dark:#15602e;
    --white:#ffffff;
    --grey:#6d6e70;
    --grid:#b9bbbd;
    --photo-warm:#c99a5a;
    --photo-dark:#3b3226;
  }
  *{margin:0;padding:0;box-sizing:border-box}
  html,body{width:1200px;height:624px;overflow:hidden;background:var(--stage)}
  body{position:relative;font-family:"Roboto",Arial,sans-serif;color:var(--white)}
  .page{position:absolute;top:90px;height:446px;overflow:hidden}
  .page--left{left:27px;width:571px;background:var(--green)}
  .page--right{left:603px;width:570px;background:var(--white)}

  /* left page */
  .segment-band{position:absolute;left:0;top:0;width:571px;height:140px;background:var(--orange)}
  .segment-title{position:absolute;left:0;width:174px;top:22px;text-align:right;font-family:"Oswald",Impact,sans-serif;font-weight:700;font-size:41px;line-height:42px;letter-spacing:.5px}
  .segment{position:absolute;top:28px;font-size:7.6px;line-height:9.6px}
  .segment h3{font-size:9px;font-weight:700;margin-bottom:2px}
  .segment::after{content:"";display:block;width:27px;height:2px;background:var(--white);margin-top:8px}
  .segment--public{left:189px;width:124px}
  .segment--engaged{left:326px;width:102px}
  .segment--athletes{left:445px;width:110px}

  .stat{position:absolute;top:155px;width:150px}
  .stat__label{position:absolute;left:0;top:0;padding-left:5px;border-left:1px solid var(--white);font-size:9px;font-weight:700;line-height:11px;height:28px}
  .stat__icon{position:absolute;top:31px;width:36px;height:36px}
  .stat__value{position:absolute;top:77px;height:22px;padding:0 6px;font-family:"Oswald",Impact,sans-serif;font-weight:700;font-size:16px;line-height:22px;background:linear-gradient(90deg,rgba(240,90,40,0) 0%,var(--orange) 45%)}
  .stat--participants{left:97px}
  .stat--participants .stat__icon{left:-7px}
  .stat--participants .stat__value{left:-70px;width:71px;text-align:right}
  .stat--sports{left:272px}
  .stat--sports .stat__icon{left:-6px}
  .stat--sports .stat__value{left:-41px;width:43px;text-align:right}
  .stat--visitors{left:447px}
  .stat--visitors .stat__icon{left:-6px}
  .stat--visitors .stat__value{left:-64px;width:66px;text-align:right}
  .stat__value sup{font-size:10px;vertical-align:4px}

  .survey{position:absolute;top:280px;width:140px}
  .survey__label{font-size:9px;font-weight:700;line-height:11px;padding-left:5px;border-left:1px solid var(--white);height:45px}
  .survey__dial{position:absolute;left:-58px;top:50px;width:98px;height:98px}
  .survey--excellent{left:98px}
  .survey--again{left:274px}
  .survey--sponsors{left:449px}

  /* right page */
  .event-photo{position:absolute;inset:0;background:
      radial-gradient(ellipse 60% 50% at 100% 0%,var(--white) 55%,rgba(255,255,255,0) 100%),
      linear-gradient(180deg,#e9dcc6 0%,var(--photo-warm) 30%,#8a6a45 60%,var(--photo-dark) 100%)}
  .growth-title{position:absolute;right:34px;top:25px;font-family:"Oswald",Impact,sans-serif;font-weight:700;font-size:23px;color:var(--grey);letter-spacing:.3px}
  .growth-table{position:absolute;left:223px;top:63px}
  .growth-row{display:flex;align-items:center;height:17px;margin-bottom:4px}
  .growth-year{width:28px;height:17px;background:var(--green);font-size:8px;line-height:17px;text-align:center;color:var(--white);margin-right:4px}
  .box{width:16px;height:17px;border:1px solid var(--grid);border-left:none;background:var(--white);position:relative}
  .box:first-of-type{border-left:1px solid var(--grid)}
  .box.on::before{content:"";position:absolute;left:3px;top:3px;width:9px;height:9px;border:1px solid var(--grey)}
  .box.on::after{content:"";position:absolute;left:6px;top:3px;width:4px;height:7px;border-right:2px solid var(--grey);border-bottom:2px solid var(--grey);transform:rotate(40deg)}
  .growth-row--current .box.on::before{border-color:var(--orange)}
  .growth-row--current .box.on::after{border-color:var(--orange)}
  .growth-count{width:54px;height:17px;margin-left:2px;padding-left:3px;font-family:"Oswald",Impact,sans-serif;font-weight:700;font-size:11px;line-height:17px;color:var(--white);background:linear-gradient(90deg,var(--green-dark) 60%,rgba(31,122,61,.15))}
  .growth-axis{position:absolute;left:526px;top:63px;height:80px;width:12px}
  .growth-axis span{position:absolute;left:0;top:40px;transform:translate(-20px,0) rotate(-90deg);font-size:7.5px;font-weight:700;color:var(--grey);white-space:nowrap;width:52px;text-align:center}
  .growth-band{position:absolute;left:0;top:365px;width:570px;height:55px;background:rgba(240,90,40,.9);text-align:right;padding-right:28px}
  .growth-band strong{display:block;font-family:"Oswald",Impact,sans-serif;font-weight:500;font-size:30px;line-height:32px;padding-top:2px}
  .growth-band span{display:block;font-family:"Oswald",Impact,sans-serif;font-weight:500;font-size:13.5px;line-height:16px}
</style>
</head>
<body>

<section class="page page--left">
  <header class="segment-band">
    <h1 class="segment-title">TARGET<br>SEGMENT</h1>
    <div class="segment segment--public">
      <h3>Mainstream Public</h3>
      <p>This is a huge audience reached predominantly through the mainstream print and digital coverage. They are captivated and inspired by the incredible feats of sport events and determination displayed by the athletes. Estimated number of mainstream audience is 50,000.</p>
    </div>
    <div class="segment segment--engaged">
      <h3>Engaged</h3>
      <p>This segment encompasses all those who are engaged directly with us, but not necessarily a current athlete.</p>
    </div>
    <div class="segment segment--athletes">
      <h3>Athletes</h3>
      <p>Majority of athletes are ranging between 20 - 45 years old, %70 Male and %30 Female , with high disposable incomes. They are fit, motivated and looking to challenge themselves.</p>
    </div>
  </header>

  <div class="stat stat--participants">
    <p class="stat__label">Number of<br>Participates in 2014</p>
    <svg class="stat__icon" viewBox="0 0 36 36" aria-hidden="true"><circle cx="18" cy="18" r="16.5" fill="none" stroke="#fff" stroke-width="1.4"/><rect x="11.5" y="11.5" width="13" height="13" fill="none" stroke="#fff" stroke-width="1.6"/><path d="M14 17.5l3 3 7-8" fill="none" stroke="#fff" stroke-width="2"/></svg>
    <p class="stat__value">10,000</p>
  </div>
  <div class="stat stat--sports">
    <p class="stat__label">Number of<br>Sports</p>
    <svg class="stat__icon" viewBox="0 0 36 36" aria-hidden="true"><circle cx="18" cy="18" r="16.5" fill="none" stroke="#fff" stroke-width="1.4"/><circle cx="17" cy="20" r="6" fill="none" stroke="#fff" stroke-width="1.6"/><path d="M17 14v-4h4M20 14l4-4" fill="none" stroke="#fff" stroke-width="1.6"/></svg>
    <p class="stat__value">13</p>
  </div>
  <div class="stat stat--visitors">
    <p class="stat__label">Visitors</p>
    <svg class="stat__icon" viewBox="0 0 36 36" aria-hidden="true"><circle cx="18" cy="18" r="16.5" fill="none" stroke="#fff" stroke-width="1.4"/><path d="M11 14h14v5H11zM12 19l-1 7M24 19l1 7M15 19l-.5 5M21 19l.5 5" fill="none" stroke="#fff" stroke-width="1.6"/></svg>
    <p class="stat__value"><sup>+</sup>30,000</p>
  </div>

  <div class="survey survey--excellent">
    <p class="survey__label">Said they would rate our<br>events as “Excellent”<br>in our survey (Average)</p>
    <svg class="survey__dial" viewBox="0 0 98 98" aria-hidden="true"><circle cx="49" cy="49" r="42" fill="none" stroke="#fff" stroke-width="10" stroke-dasharray="1 2.3"/><circle cx="49" cy="49" r="31" fill="#fff" stroke="#f05a28" stroke-width="5"/><text x="49" y="55.5" text-anchor="middle" font-family="Oswald, Impact, sans-serif" font-weight="700" font-size="17" fill="#f05a28">86%</text></svg>
  </div>
  <div class="survey survey--again">
    <p class="survey__label">Said they would<br>participate<br>again (Average)</p>
    <svg class="survey__dial" viewBox="0 0 98 98" aria-hidden="true"><circle cx="49" cy="49" r="42" fill="none" stroke="#fff" stroke-width="10" stroke-dasharray="1 2.3"/><circle cx="49" cy="49" r="31" fill="#fff" stroke="#f05a28" stroke-width="5"/><text x="49" y="55.5" text-anchor="middle" font-family="Oswald, Impact, sans-serif" font-weight="700" font-size="17" fill="#f05a28">84%</text></svg>
  </div>
  <div class="survey survey--sponsors">
    <p class="survey__label">Said they<br>recognized our<br>sponsors (Average)</p>
    <svg class="survey__dial" viewBox="0 0 98 98" aria-hidden="true"><circle cx="49" cy="49" r="42" fill="none" stroke="#fff" stroke-width="10" stroke-dasharray="1 2.3"/><circle cx="49" cy="49" r="31" fill="#fff" stroke="#f05a28" stroke-width="5"/><text x="49" y="55.5" text-anchor="middle" font-family="Oswald, Impact, sans-serif" font-weight="700" font-size="17" fill="#f05a28">80%</text></svg>
  </div>
</section>

<section class="page page--right">
  <div class="event-photo" role="img" aria-label="Event photo: host in a green T-shirt speaking into a microphone beside the course barrier, with a crowd of spectators behind"></div>
  <h2 class="growth-title">GROWTH OVER THE YEARS</h2>

  <div class="growth-table">
    <div class="growth-row">
      <span class="growth-year">2011</span>
      <span class="box on"></span><span class="box on"></span><span class="box"></span><span class="box"></span><span class="box"></span><span class="box"></span><span class="box"></span><span class="box"></span><span class="box"></span><span class="box"></span><span class="box"></span><span class="box"></span><span class="box"></span>
      <span class="growth-count">1,300</span>
    </div>
    <div class="growth-row">
      <span class="growth-year">2012</span>
      <span class="box on"></span><span class="box on"></span><span class="box on"></span><span class="box on"></span><span class="box"></span><span class="box"></span><span class="box"></span><span class="box"></span><span class="box"></span><span class="box"></span><span class="box"></span><span class="box"></span><span class="box"></span>
      <span class="growth-count">2,700</span>
    </div>
    <div class="growth-row">
      <span class="growth-year">2013</span>
      <span class="box on"></span><span class="box on"></span><span class="box on"></span><span class="box on"></span><span class="box on"></span><span class="box on"></span><span class="box on"></span><span class="box on"></span><span class="box on"></span><span class="box"></span><span class="box"></span><span class="box"></span><span class="box"></span>
      <span class="growth-count">5,800+</span>
    </div>
    <div class="growth-row growth-row--current">
      <span class="growth-year">2014</span>
      <span class="box on"></span><span class="box on"></span><span class="box on"></span><span class="box on"></span><span class="box on"></span><span class="box on"></span><span class="box on"></span><span class="box on"></span><span class="box on"></span><span class="box on"></span><span class="box on"></span><span class="box on"></span><span class="box on"></span>
      <span class="growth-count">10,000+</span>
    </div>
  </div>
  <div class="growth-axis"><span>Participants</span></div>

  <div class="growth-band">
    <strong>42%</strong>
    <span>PARTICIPANTS GROWTH IN LAST 2 YEARS</span>
  </div>
</section>

</body>
</html>
```